High-end construction company needs a business card design

We need a modern looking business card that draws people in, is memorable and looks so good people will want to sick it on their fridges.
On the first side what is needed are:
Logo
My name - Tomasz Brelwik
Title - Managing Director
Website - www.varkelt.co.uk
Email - tomasz@varkelt.co.uk
Telephone - 020 5194 6281
Mobile - 07845139072
On the back side was is needed is a list of all the services we provide:
-Kitchen Renovations
-Bathroom Renovations
-House Renovations
-Garage Conversions
-Extensions
-Loft Conversions
-Conservatories
-Carpentry
-Tiling
-Electrical
-Plumbing & Heating
-Bricklaying
-Landscaping
-Decorating
-Plastering
We would like the colours to be the same shades as on the logo with grey or black for the words.
Target Market(s)
Anyone who needs building work done
Contact Information for Business Card
This business card is for a construction company which strives to deliver excellent service and quality.
The look and feel of the card should represent this.
Requirements
Must have
- On the first side what is needed are:
Logo
My name - Tomasz Brelwik
Title - Managing Director
Website - www.varkelt.co.uk
Email - tomasz@varkelt.co.uk
Telephone - 020 5194 6281
Mobile - 07845139072
Nice to have
- Cool looking features

```html
<!DOCTYPE html>
<html lang="en">
<head>
<meta charset="utf-8">
<title>Varkelt Construction Ltd – Business Card</title>
<link href="https://fonts.googleapis.com/css2?family=Exo:wght@400;500;600&display=swap" rel="stylesheet">
<style>
  :root {
    --page-bg: #e6e6e4;
    --card-bg: #4b4b4d;
    --brand-green: #7ed957;
    --text-light: #dcdcdc;
    --text-muted: #b9b9b9;
    --rule: #a9a9a9;
  }
  * { box-sizing: border-box; margin: 0; padding: 0; }
  html, body {
    width: 1200px; height: 1100px; overflow: hidden;
    background: var(--page-bg);
    font-family: "Exo", sans-serif;
  }
  .sheet {
    width: 1200px; height: 1100px;
    display: flex; flex-direction: column; align-items: center; justify-content: center;
    gap: 40px;
  }
  .card {
    position: relative;
    width: 860px; height: 491px;
    background: var(--card-bg);
    border-radius: 4px;
    box-shadow: 0 10px 28px rgba(0,0,0,0.18);
    color: var(--text-light);
    letter-spacing: 0.06em;
  }

  /* Front */
  .holder { position: absolute; left: 64px; top: 150px; }
  .holder__name { font-size: 34px; font-weight: 600; }
  .holder__title { font-size: 20px; font-weight: 500; color: var(--text-muted); margin-top: 4px; letter-spacing: 0.12em; }

  .brand {
    position: absolute; right: 64px; top: 110px;
    display: flex; align-items: center; gap: 14px;
  }
  .brand__mark { width: 26px; height: 26px; border-radius: 50%; background: var(--brand-green); }
  .brand__name {
    color: var(--brand-green); font-weight: 600; font-size: 30px;
    letter-spacing: 0.08em; text-transform: uppercase; line-height: 1.15;
  }

  .online { position: absolute; right: 64px; top: 300px; font-size: 22px; line-height: 1.55; font-weight: 500; }
  .phones { position: absolute; left: 64px; bottom: 56px; font-size: 26px; line-height: 1.45; font-weight: 500; letter-spacing: 0.1em; }

  /* Back */
  .services { position: absolute; left: 64px; top: 56px; right: 64px; }
  .services__label { font-size: 20px; color: var(--text-muted); font-weight: 500; letter-spacing: 0.12em; }
  .services__rule { height: 1px; background: var(--rule); width: 230px; margin: 10px 0 14px 20px; }
  .services__cols { display: flex; gap: 70px; padding-left: 20px; }
  .services__list { list-style: none; font-size: 21px; line-height: 1.6; font-weight: 500; }
  .services__list--second { margin-top: -40px; }
  .services__list--second::before {
    content: ""; display: block; height: 1px; width: 120px; background: var(--rule); margin-bottom: 10px;
  }
  .back-footer {
    position: absolute; left: 64px; right: 64px; bottom: 46px;
    display: flex; align-items: center; gap: 18px;
  }
  .back-footer__rule { flex: 1; height: 1px; background: var(--rule); }
  .back-footer__name { color: var(--brand-green); font-weight: 600; font-size: 14px; letter-spacing: 0.1em; text-transform: uppercase; }
</style>
</head>
<body>
<main class="sheet">
  <section class="card card--front" aria-label="Business card front">
    <div class="brand">
      <span class="brand__mark"></span>
      <span class="brand__name">Varkelt<br>Construction Ltd</span>
    </div>
    <div class="holder">
      <p class="holder__name">Tomasz Brelwik</p>
      <p class="holder__title">Managing Director</p>
    </div>
    <div class="online">
      <p>www.varkelt.co.uk</p>
      <p>tomasz@varkelt.co.uk</p>
    </div>
    <div class="phones">
      <p>020 5194 6281</p>
      <p>078 4513 9072</p>
    </div>
  </section>

  <section class="card card--back" aria-label="Business card back">
    <div class="services">
      <p class="services__label">Services</p>
      <div class="services__rule"></div>
      <div class="services__cols">
        <ul class="services__list">
          <li>Kitchen Renovations</li>
          <li>Bathroom Renovations</li>
          <li>House Renovations</li>
          <li>Garage Conversions</li>
          <li>Extensions</li>
          <li>Loft Conversions</li>
          <li>Conservatories</li>
          <li>Carpentry</li>
        </ul>
        <ul class="services__list services__list--second">
          <li>Tiling</li>
          <li>Electrical</li>
          <li>Plumbing &amp; Heating</li>
          <li>Bricklaying</li>
          <li>Landscaping</li>
          <li>Decorating</li>
          <li>Plastering</li>
        </ul>
      </div>
    </div>
    <div class="back-footer">
      <div class="back-footer__rule"></div>
      <span class="back-footer__name">Varkelt Construction Ltd</span>
    </div>
  </section>
</main>
</body>
</html>
```